Design a Job Application & CV

I need a design for upcoming job applications that includes a cv. It needs to look as elegant and modern as possible as the application will be send mainly to large corporations and strategy consultancies. I have attached an application that I like for your consideration. One of the more difficult requirements is that it needs to be editable in ms office word for mac/windows.
As stated only the design is part of this project. I will fill in my content later on.
Reason: Dear Designers,
I am going to increase the budget as well as extending the deadline. I am hoping that you can improve upon the design that I have provided in the brief. If you have questions please let me know.
Dear Designers,
Target Market(s)
Human Resources Managers, Senior Consultants and Executives of larger firms
Industry/Entity Type
Office
Requirements
Must have
- 4 Pages including( a cover page, a coverletter page, 2 pages cv)
It should be easy to edit and should be readable by word for mac, i.e. in the *.docx format.
Here is an example of what I like:
http://www.torvenmald.example/applicationexample.pdf
http://www.torvenmald.example/applicationExample.docx
colors that I like are blue, grey, black, white
Nice to have
- icons to indicate sections
Should not have
- invasive cliparts

```html
<!DOCTYPE html>
<html lang="en">
<head>
<meta charset="utf-8">
<title>Job Application &amp; CV Template</title>
<link rel="stylesheet" href="https://fonts.googleapis.com/css2?family=Open+Sans:wght@400;600;700&display=swap">
<style>
:root{
  --stage-top:#5a5c5f;
  --stage-bottom:#2e2f31;
  --ink:#2b2b2b;
  --muted:#7a7a7a;
  --soft:#a9a9a9;
  --blue:#1a9ee0;
  --blue-light:#9fd6f2;
  --blue-pale:#cfeaf8;
  --charcoal-top:#4a4b4d;
  --charcoal-bottom:#1f2021;
  --paper:#ffffff;
  --rule:#e3e3e3;
}
*{box-sizing:border-box;margin:0;padding:0}
html,body{width:900px;height:1200px;overflow:hidden}
body{
  font-family:"Open Sans",Arial,sans-serif;
  background:linear-gradient(180deg,var(--stage-top),var(--stage-bottom));
  position:relative;color:var(--ink);
}
.page{position:absolute;background:var(--paper);overflow:hidden;box-shadow:0 2px 10px rgba(0,0,0,.35)}
.page--cv-dark{left:40px;top:14px;width:410px;height:576px}
.page--cv-blue{left:456px;top:14px;width:412px;height:576px}
.page--letter{left:40px;top:612px;width:410px;height:576px}
.page--cover{left:456px;top:612px;width:412px;height:576px}

/* CV header */
.cv-header{height:64px;position:relative;padding:14px 20px}
.cv-header--dark{background:linear-gradient(180deg,var(--charcoal-top),var(--charcoal-bottom))}
.cv-header--blue{background:var(--blue)}
.cv-title{font-size:30px;font-weight:400;line-height:1;margin-top:10px}
.cv-header--dark .cv-title{color:#fff}
.cv-header--blue .cv-title{color:var(--charcoal-bottom)}
.cv-source{position:absolute;right:14px;top:6px;font-size:5.5px;color:#fff}
.cv-rule{height:3px;background:var(--blue-pale);margin:0}
.page--cv-blue .cv-rule{background:var(--rule)}

.cv-body{padding:26px 22px 0 22px}
.cv-section{display:grid;grid-template-columns:138px 1fr;column-gap:12px;margin-bottom:18px}
.cv-heading{grid-column:1;text-align:right;color:var(--blue);font-size:11px;font-weight:600}
.cv-heading--solo{grid-column:1 / span 2;text-align:left;padding-left:70px;margin-bottom:6px}
.cv-text{font-size:5.5px;color:var(--muted);line-height:1.5}
.cv-label{text-align:right;font-size:5.5px;color:var(--muted);line-height:1.5}
.cv-label strong{color:var(--ink);font-weight:600}
.cv-entry{margin-bottom:12px}
.cv-list{list-style:none;font-size:5.5px;color:var(--muted);line-height:1.55}
.cv-list li::before{content:"\2022  "}
.cv-head-left{text-align:left;padding-left:42px;grid-column:1 / span 2;margin-bottom:6px}

/* Cover letter */
.letter-band{height:38px;background:linear-gradient(180deg,#f2f2f2,#e2e2e2);padding:12px 20px}
.letter-title{font-size:14px;color:#555;font-weight:400}
.letter-bar{height:6px;background:var(--blue-pale);margin-top:4px}
.letter-bar--mid{background:var(--blue-light);height:3px;margin-top:3px}
.letter-body{padding:14px 22px;font-size:6px;color:#444;line-height:1.55}
.letter-date{text-align:right;margin-bottom:10px;color:var(--muted)}
.letter-body p{margin-bottom:9px}

/* Cover page */
.cover-top{height:176px;background:linear-gradient(180deg,var(--charcoal-top),var(--charcoal-bottom));position:relative}
.cover-title{position:absolute;left:22px;bottom:14px;color:#fff;font-size:34px;font-weight:400}
.cover-band{height:34px;background:var(--blue);padding:9px 22px;color:#fff;font-size:12px;font-weight:700}
.cover-contact{padding:34px 22px}
.cover-name{font-size:16px;color:var(--ink)}
.cover-name span{color:var(--blue)}
.cover-lines{font-size:6px;color:var(--muted);line-height:1.6;margin-top:6px}
.cover-foot{position:absolute;left:0;right:0;bottom:18px}
.cover-foot .letter-bar{margin-top:3px}
</style>
</head>
<body>

<section class="page page--cv-dark">
  <header class="cv-header cv-header--dark">
    <p class="cv-source">Text Name (Source client if you wish)</p>
    <h1 class="cv-title">Text Here</h1>
  </header>
  <div class="cv-rule"></div>
  <div class="cv-body">
    <div class="cv-section">
      <h2 class="cv-heading">Objective</h2>
      <p class="cv-text">Lorem ipsum dolor sit amet, consectetur adipiscing elit, sed do eiusmod tempor incididunt ut labore et dolore magna aliqua enim minim.</p>
    </div>
    <div class="cv-section">
      <h2 class="cv-heading cv-head-left">Personal Info</h2>
      <p class="cv-label">Nationality<br>Birthday<br>Birthplace</p>
      <p class="cv-text">(Right click and click on personal info)</p>
    </div>
    <div class="cv-section">
      <h2 class="cv-heading cv-head-left">Employment</h2>
      <p class="cv-label"><strong>Job Position</strong><br>Company</p>
      <div class="cv-entry">
        <p class="cv-text">2000-2010<br>Company name</p>
        <ul class="cv-list"><li>Description</li><li>Description</li><li>Description</li><li>Description</li></ul>
      </div>
      <p class="cv-label"><strong>Job Position</strong><br>Company</p>
      <div class="cv-entry">
        <p class="cv-text">2000-2010<br>Company name</p>
        <ul class="cv-list"><li>Description</li><li>Description</li><li>Description</li><li>Description</li></ul>
      </div>
    </div>
    <div class="cv-section">
      <h2 class="cv-heading cv-head-left">Education</h2>
      <p class="cv-label"><strong>BB Mass Communication</strong><br>College/University</p>
      <div class="cv-entry">
        <p class="cv-text">2000-2004<br>Grade</p>
        <ul class="cv-list"><li>Description</li><li>Description</li><li>Description</li></ul>
      </div>
    </div>
  </div>
</section>

<section class="page page--cv-blue">
  <header class="cv-header cv-header--blue">
    <p class="cv-source">Text Name (Source client if you wish)</p>
    <h1 class="cv-title">Text Here</h1>
  </header>
  <div class="cv-rule"></div>
  <div class="cv-body">
    <div class="cv-section">
      <h2 class="cv-heading">Objective</h2>
      <p class="cv-text">Lorem ipsum dolor sit amet, consectetur adipiscing elit, sed do eiusmod tempor incididunt ut labore et dolore magna aliqua enim minim.</p>
    </div>
    <div class="cv-section">
      <h2 class="cv-heading cv-head-left">Personal Info</h2>
      <p class="cv-label">Nationality<br>Birthday<br>Birthplace</p>
      <p class="cv-text">(Right click and click on personal info)</p>
    </div>
    <div class="cv-section">
      <h2 class="cv-heading cv-head-left">Employment</h2>
      <p class="cv-label"><strong>JOB POSITION</strong><br>Company</p>
      <div class="cv-entry">
        <p class="cv-text">2000-2010<br>Company name</p>
        <ul class="cv-list"><li>Description</li><li>Description</li><li>Description</li><li>Description</li></ul>
      </div>
      <p class="cv-label"><strong>JOB POSITION</strong><br>Company</p>
      <div class="cv-entry">
        <p class="cv-text">2000-2010<br>Company name</p>
        <ul class="cv-list"><li>Description</li><li>Description</li><li>Description</li><li>Description</li></ul>
      </div>
    </div>
    <div class="cv-section">
      <h2 class="cv-heading cv-head-left">Education</h2>
      <p class="cv-label"><strong>BB Mass Communication</strong><br>College/University</p>
      <div class="cv-entry">
        <p class="cv-text">2000-2004<br>Grade</p>
        <ul class="cv-list"><li>Description</li><li>Description</li><li>Description</li></ul>
      </div>
    </div>
  </div>
</section>

<section class="page page--letter">
  <header class="letter-band"><h1 class="letter-title">Coverletter</h1></header>
  <div class="letter-bar"></div>
  <div class="letter-bar letter-bar--mid"></div>
  <div class="letter-body">
    <p class="letter-date">Date</p>
    <p>Dear Sir,</p>
    <p>Lorem ipsum dolor sit amet, consectetur adipiscing elit. Praesent mauris, sit at vestibulum fringilla. Quisque convallis, nisl eget luctus tempor, nibh mauris dictum nibh, sed laoreet magna est sit amet orci. Sed vestibulum tellus nec mauris tincidunt, quis ultrices risus varius. Integer posuere elit sed nunc porta, id facilisis arcu dapibus.</p>
    <p>Suspendisse potenti. Nam ut ante vel dolor pulvinar vehicula. Phasellus nec justo non lectus finibus consequat. Vivamus sodales, lorem quis aliquet commodo, metus velit blandit nibh, eu feugiat lorem arcu a purus. Curabitur fermentum nisi in tellus hendrerit, a tempor nulla lobortis. Donec imperdiet velit non orci porttitor, ac aliquet massa eleifend.</p>
    <p>Maecenas dictum sapien ut lacus faucibus, vel rutrum neque volutpat. Aenean eu ligula vitae erat consectetur efficitur. Morbi ac turpis sit amet nibh euismod suscipit. Nulla facilisi. Etiam vel dui at ipsum aliquam pretium sed eget lorem. Pellentesque habitant morbi tristique senectus et netus.</p>
    <p>Phasellus nec ante. Fusce et interdum nisi, sed tempus lectus. Integer laoreet, enim ac accumsan aliquet, nisl dolor gravida metus, non vehicula magna nisi id ante.</p>
    <p>Sincerely,</p>
    <p>Best regards</p>
  </div>
</section>

<section class="page page--cover">
  <header class="cover-top"><h1 class="cover-title">Application</h1></header>
  <div class="cover-band">Job Position Here</div>
  <div class="cover-contact">
    <p class="cover-name">John <span>Doe</span></p>
    <p class="cover-lines">1234 Harbor Avenue, Apt 12<br>Rivertown, RT 90000<br>Phone +1 (555) 012-3456<br>E-Mail name@example.com</p>
  </div>
  <div class="cover-foot">
    <div class="letter-bar"></div>
    <div class="letter-bar letter-bar--mid"></div>
  </div>
</section>

</body>
</html>
```